Animal Eye Clinic needs a Business card

We are a new veterinary ophthalmology practice (Ridgeline Pet Vision Care) and we need a business card designed. We only see animal eyes - we are not a regular veterinary clinic. We already have a logo. We are looking for a professional, good looking business card to hand out to our clients. We are looking for something simple but professional and contemporary. Our logo is likely the only picture/graphic that needs to be on the card.
Updates

Contact Information for Business Card

Delia Vossman, BSc, DVM, MSc, DipACVO
Veterinary Ophthalmologist

Phone: 250.418.3927
Email: ridgelinepetvisioncare@mailbox-example.net
Website: ridgelinepetvisioncare-example.net
Address: 1874 Thornbury Rd
Kelowna, BC, V1X 4M9

Colors

Designer to choose colors to be used in the design.

Requirements
Must have
• Our logo (attached)

```html
<!DOCTYPE html>
<html lang="en">
<head>
<meta charset="utf-8">
<title>Ridgeline Pet Vision Care – Business Card</title>
<link href="https://fonts.googleapis.com/css2?family=Roboto:wght@300;400;500;700&display=swap" rel="stylesheet">
<style>
  :root {
    --teal: #1b97a6;
    --slate: #6b6b6b;
    --ink: #555555;
    --paper: #ffffff;
    --backdrop: #d9dcdf;
  }
  * { box-sizing: border-box; margin: 0; padding: 0; }
  html, body {
    width: 1200px; height: 800px; overflow: hidden;
    background: var(--backdrop);
    font-family: "Roboto", Arial, sans-serif;
  }
  .card {
    position: absolute;
    width: 600px; height: 343px;
    background: var(--paper);
    box-shadow: 0 6px 18px rgba(0,0,0,0.18);
    overflow: hidden;
  }
  /* Front */
  .card-front { left: 440px; top: 40px; }
  .brand {
    position: absolute; left: 0; right: 0; top: 120px;
    display: flex; align-items: center; justify-content: center; gap: 14px;
  }
  .brand-dot {
    width: 46px; height: 46px; border-radius: 50%;
    background: var(--teal);
  }
  .brand-name {
    color: var(--teal); font-weight: 500; font-size: 30px;
    text-transform: uppercase; letter-spacing: 0.5px;
  }
  .front-web {
    position: absolute; left: 0; right: 0; top: 245px;
    text-align: center; color: var(--teal);
    font-size: 15px; letter-spacing: 2.5px;
  }
  /* Back */
  .card-back { left: 160px; top: 417px; }
  .artwork { position: absolute; left: 0; top: 0; width: 600px; height: 343px; }
  .back-name {
    position: absolute; left: 26px; top: 28px;
    color: var(--paper); font-weight: 500; font-size: 15px;
    text-transform: uppercase; letter-spacing: 0.5px; width: 240px; line-height: 1.25;
  }
  .details {
    position: absolute; right: 26px; top: 128px;
    text-align: right; color: var(--ink);
  }
  .person-name {
    color: var(--teal); font-weight: 700; font-size: 24px;
    text-transform: uppercase; letter-spacing: 0.5px;
  }
  .credentials { color: var(--teal); font-weight: 700; font-size: 13px; margin-top: 2px; }
  .role { font-size: 15px; margin-top: 2px; }
  .address { font-size: 15px; line-height: 1.3; margin-top: 16px; }
  .contacts { list-style: none; margin-top: 14px; font-size: 15px; line-height: 1.35; }
  .contacts li { display: flex; align-items: center; justify-content: flex-end; gap: 8px; }
  .contacts svg { width: 14px; height: 14px; flex: none; }
</style>
</head>
<body>

<section class="card card-front" aria-label="Business card front">
  <div class="brand">
    <span class="brand-dot"></span>
    <span class="brand-name">Ridgeline Pet Vision Care</span>
  </div>
  <p class="front-web">ridgelinepetvisioncare-example.net</p>
</section>

<section class="card card-back" aria-label="Business card back">
  <svg class="artwork" viewBox="0 0 600 343" role="img" aria-label="Teal panel where the clinic's animal silhouette artwork belongs">
    <path d="M0 0 H318 Q300 60 300 140 Q295 220 230 260 Q170 295 110 343 H0 Z" fill="var(--teal)"/>
    <path d="M110 343 Q160 302 200 272 L222 296 Q190 322 160 343 Z" fill="var(--slate)"/>
  </svg>
  <p class="back-name">Ridgeline Pet Vision Care</p>

  <div class="details">
    <p class="person-name">Delia Vossman</p>
    <p class="credentials">BSc, DVM, MSc, DipACVO</p>
    <p class="role">Veterinary Ophthalmologist</p>
    <p class="address">1874 Thornbury Rd<br>Kelowna, BC, V1X 4M9</p>
    <ul class="contacts">
      <li>250.418.3927
        <svg viewBox="0 0 24 24" aria-hidden="true"><path fill="var(--teal)" d="M6.6 10.8a15 15 0 0 0 6.6 6.6l2.2-2.2a1 1 0 0 1 1-.25 11.4 11.4 0 0 0 3.6.57 1 1 0 0 1 1 1V20a1 1 0 0 1-1 1A17 17 0 0 1 3 4a1 1 0 0 1 1-1h3.5a1 1 0 0 1 1 1c0 1.25.2 2.45.57 3.57a1 1 0 0 1-.25 1z"/></svg>
      </li>
      <li>ridgelinepetvisioncare@mailbox-example.net
        <svg viewBox="0 0 24 24" aria-hidden="true"><rect x="2" y="5" width="20" height="14" fill="none" stroke="var(--teal)" stroke-width="2"/><path d="M2 5l10 8 10-8" fill="none" stroke="var(--teal)" stroke-width="2"/></svg>
      </li>
      <li>ridgelinepetvisioncare-example.net
        <svg viewBox="0 0 24 24" aria-hidden="true"><g fill="none" stroke="var(--teal)" stroke-width="1.8"><circle cx="12" cy="12" r="10"/><ellipse cx="12" cy="12" rx="4.5" ry="10"/><path d="M2 12h20M4 7h16M4 17h16"/></g></svg>
      </li>
    </ul>
  </div>
</section>

</body>
</html>
```